An internal sign in a physiotherapy clinic with gym. About working hard

We are a physiotherapy clinic / gym and we are wanting an internal wall to be a large sign with a great slogan
We are after 3 parts to it
1. The image / backdrop
2. The slogan
3. Our clinic logo

I have attached some images of the concept of what we are after. It can be climbing a mountain, rockclimbing and even hard work in a gym.

The slogan is:
"IF IT DOESN'T CHALLENGE YOU, IT WON'T CHANGE YOU"

Logo
I have attached a few different versions of our logo to assist you in the sign based on the background

THE SIGN SIZE WILL BE:
2935mm wide x 1885mm high

```html
<!DOCTYPE html>
<html lang="en">
<head>
<meta charset="utf-8">
<title>Kestrel Sports Medicine – Wall Sign</title>
<link rel="stylesheet" href="https://fonts.googleapis.com/css2?family=Saira+Condensed:wght@700;800&family=Poppins:wght@400;600;700&display=swap">
<style>
  :root {
    --page-bg: #d9d9d9;
    --sign-bg: #000000;
    --brand-blue: #4cc3ea;
    --text-white: #ffffff;
    --photo-skin: #6a5140;
    --photo-warm: #3e3029;
    --photo-dark: #1a1918;
    --photo-shadow: #0c0c0c;
  }
  html, body {
    margin: 0;
    padding: 0;
    width: 800px;
    height: 1200px;
    overflow: hidden;
    background: var(--page-bg);
  }
  .canvas {
    position: relative;
    width: 800px;
    height: 1200px;
  }
  .wall-sign {
    position: absolute;
    left: 30px;
    top: 362px;
    width: 740px;
    height: 475px;
    background: var(--sign-bg);
    overflow: hidden;
  }
  .hero-photo {
    position: absolute;
    left: 170px;
    top: 0;
    width: 570px;
    height: 475px;
    background:
      linear-gradient(90deg, var(--sign-bg) 0%, rgba(0,0,0,0.85) 22%, rgba(0,0,0,0) 48%),
      linear-gradient(180deg, var(--sign-bg) 0%, rgba(0,0,0,0) 14%),
      radial-gradient(ellipse 30% 34% at 62% 70%, var(--photo-skin) 0%, rgba(106,81,64,0) 100%),
      radial-gradient(ellipse 22% 16% at 55% 42%, rgba(106,81,64,0.8) 0%, rgba(106,81,64,0) 100%),
      radial-gradient(ellipse 18% 30% at 88% 40%, rgba(106,81,64,0.55) 0%, rgba(106,81,64,0) 100%),
      linear-gradient(170deg, rgba(0,0,0,0) 20%, rgba(140,140,140,0.28) 24%, rgba(0,0,0,0) 28%),
      radial-gradient(ellipse 60% 60% at 62% 62%, var(--photo-warm) 0%, var(--photo-dark) 60%, var(--photo-shadow) 100%);
  }
  .sign-type {
    position: absolute;
    inset: 0;
    width: 740px;
    height: 475px;
  }
  .brand-name, .brand-tagline, .web-address {
    font-family: "Poppins", sans-serif;
  }
  .brand-name {
    font-weight: 700;
    fill: var(--text-white);
  }
  .brand-tagline {
    font-weight: 400;
    fill: var(--brand-blue);
  }
  .brand-mark { fill: var(--brand-blue); }
  .slogan {
    font-family: "Saira Condensed", sans-serif;
    font-style: italic;
    font-weight: 800;
  }
  .slogan-white { fill: var(--text-white); }
  .slogan-blue { fill: var(--brand-blue); }
  .slogan-outline {
    fill: none;
    stroke: var(--brand-blue);
    stroke-width: 1.4;
  }
  .web-address {
    font-weight: 400;
    fill: var(--text-white);
  }
  .web-address .highlight {
    font-weight: 600;
    fill: var(--brand-blue);
  }
</style>
</head>
<body>
<main class="canvas">
  <section class="wall-sign">
    <div class="hero-photo" role="img" aria-label="Dark gym photograph of a man straining through a lat pulldown, bar held overhead"></div>

    <svg class="sign-type" viewBox="0 0 740 475" xmlns="http://www.w3.org/2000/svg">
      <g class="brand">
        <circle class="brand-mark" cx="100" cy="84" r="13"/>
        <text class="brand-name" x="126" y="89" font-size="28" textLength="204" lengthAdjust="spacingAndGlyphs">KESTREL</text>
        <text class="brand-tagline" x="127" y="106" font-size="11" textLength="203" lengthAdjust="spacing">SPORTS MEDICINE</text>
      </g>

      <g class="slogan">
        <text class="slogan-white" x="57" y="190" font-size="38" textLength="236" lengthAdjust="spacingAndGlyphs">IF IT DOESN'T</text>
        <text x="46" y="292" font-size="126" textLength="390" lengthAdjust="spacingAndGlyphs"><tspan class="slogan-blue">CHALLEN</tspan><tspan class="slogan-outline">GE</tspan></text>
        <text class="slogan-blue" x="46" y="359" font-size="71" textLength="134" lengthAdjust="spacingAndGlyphs">YOU</text>
        <text class="slogan-white" x="196" y="330" font-size="30" textLength="128" lengthAdjust="spacingAndGlyphs">IT WON'T</text>
        <text class="slogan-white" x="192" y="359" font-size="30" textLength="179" lengthAdjust="spacingAndGlyphs">CHANGE YOU</text>
      </g>

      <text class="web-address" x="43" y="421" font-size="15" textLength="311" lengthAdjust="spacingAndGlyphs">www.<tspan class="highlight">kestrelsportsmedicine</tspan>.com.au</text>
    </svg>
  </section>
</main>
</body>
</html>
```